Business Card Design Project

i need a bussines car design
Velora Clinical Hypnotherapy

Daniel Wexford
Psychotherapy & Hypnosis

84261937 /0427591628

back of the card appoinment space.

file was provided on a PDF, LOgo , use the blu colorsa as well , elegant, clear,

Target Market(s)

young professional, caucasian , young mothers.

Industry/Entity Type

Business

```html
<!DOCTYPE html>
<html lang="en">
<head>
<meta charset="utf-8">
<title>Velora Hypnotherapy – Business Card, Front and Back</title>
<link rel="stylesheet" href="https://fonts.googleapis.com/css2?family=Didact+Gothic&family=Open+Sans:ital,wght@0,400;0,700;1,400&display=swap">
<style>
  :root {
    --page-bg: #e9ecef;
    --card-top: #0a3a6b;
    --card-bottom: #0d4a86;
    --frame-blue: #8dbbe6;
    --photo-tone-a: #e8dccd;
    --photo-tone-b: #c9b7a3;
    --text-white: #ffffff;
    --text-soft: #dbe7f4;
    --back-bg: #ffffff;
    --back-text: #3a3f45;
    --back-line: #8a9098;
  }
  * { box-sizing: border-box; margin: 0; padding: 0; }
  html, body {
    width: 1200px;
    height: 880px;
    overflow: hidden;
    background: var(--page-bg);
  }
  .canvas {
    position: relative;
    width: 1200px;
    height: 880px;
  }
  .card {
    position: absolute;
    left: 260px;
    width: 680px;
    height: 390px;
    border-radius: 30px;
    font-family: "Open Sans", sans-serif;
  }

  /* Front */
  .card-front {
    top: 35px;
    background: linear-gradient(160deg, var(--card-top) 0%, var(--card-bottom) 100%);
    color: var(--text-white);
  }
  .portrait-frame {
    position: absolute;
    left: 84px;
    top: 40px;
    width: 140px;
    height: 134px;
    border-radius: 12px;
    background: var(--frame-blue);
    padding: 7px;
  }
  .portrait-placeholder {
    width: 100%;
    height: 100%;
    border-radius: 8px;
    background: linear-gradient(180deg, var(--photo-tone-a) 0%, var(--photo-tone-b) 100%);
  }
  .person-name {
    position: absolute;
    left: 72px;
    top: 210px;
    font-size: 18px;
    font-weight: 700;
    letter-spacing: 0.4px;
    color: var(--text-soft);
  }
  .person-role {
    position: absolute;
    left: 66px;
    top: 238px;
    font-size: 14px;
    font-style: italic;
    color: var(--text-soft);
  }
  .contact-list {
    position: absolute;
    left: 54px;
    top: 284px;
    list-style: none;
  }
  .contact-item {
    display: flex;
    align-items: center;
    gap: 8px;
    height: 26px;
    font-size: 14px;
    font-style: italic;
    color: var(--text-soft);
  }
  .contact-icon { width: 15px; height: 18px; }
  .brand-block {
    position: absolute;
    left: 330px;
    right: 40px;
    top: 150px;
  }
  .brand-name {
    display: flex;
    align-items: center;
    gap: 10px;
    font-family: "Didact Gothic", sans-serif;
    font-size: 28px;
    color: var(--text-white);
    padding-bottom: 4px;
    border-bottom: 1.5px solid var(--text-soft);
    white-space: nowrap;
  }
  .brand-dot {
    width: 16px;
    height: 16px;
    border-radius: 50%;
    background: var(--text-white);
    flex: none;
  }
  .brand-url {
    margin-top: 4px;
    font-size: 11px;
    letter-spacing: 0.9px;
    color: var(--text-white);
  }

  /* Back */
  .card-back {
    top: 455px;
    background: var(--back-bg);
    color: var(--back-text);
    box-shadow: 0 0 0 1px #d5dae0;
    padding: 34px 48px;
  }
  .back-header { font-size: 12px; line-height: 1.6; }
  .back-title { font-size: 14px; font-weight: 700; letter-spacing: 1.5px; }
  .appointments-title {
    margin-top: 16px;
    font-size: 14px;
    font-weight: 700;
  }
  .appointment-grid {
    margin-top: 14px;
    display: grid;
    grid-template-columns: 1fr 1fr;
    column-gap: 48px;
    row-gap: 18px;
  }
  .appointment-row {
    display: flex;
    align-items: flex-end;
    gap: 4px;
    font-size: 13px;
    color: var(--back-line);
  }
  .blank {
    display: inline-block;
    height: 14px;
    border-bottom: 1.5px solid var(--back-line);
  }
  .blank-date { width: 34px; }
  .blank-time { width: 40px; margin-left: 14px; }
</style>
</head>
<body>
  <main class="canvas">
    <section class="card card-front" aria-label="Business card front">
      <div class="portrait-frame">
        <div class="portrait-placeholder" role="img" aria-label="Portrait photograph of the therapist"></div>
      </div>

      <h1 class="person-name">DANIEL WEXFORD</h1>
      <p class="person-role">Psychotherapy &amp; Hypnosis</p>

      <ul class="contact-list">
        <li class="contact-item">
          <svg class="contact-icon" viewBox="0 0 22 26" aria-hidden="true">
            <rect x="5" y="2" width="12" height="22" rx="2.5" fill="none" stroke="#dbe7f4" stroke-width="2"/>
            <line x1="9" y1="20" x2="13" y2="20" stroke="#dbe7f4" stroke-width="2"/>
          </svg>
          <span>0427 591 628</span>
        </li>
        <li class="contact-item">
          <svg class="contact-icon" viewBox="0 0 22 26" aria-hidden="true">
            <rect x="2" y="8" width="18" height="15" rx="2" fill="#dbe7f4"/>
            <path d="M3 7 Q11 1 19 7 L17 9 Q11 5 5 9 Z" fill="#dbe7f4"/>
            <g fill="#0b4179">
              <rect x="6" y="12" width="3" height="2"/><rect x="10" y="12" width="3" height="2"/><rect x="14" y="12" width="3" height="2"/>
              <rect x="6" y="16" width="3" height="2"/><rect x="10" y="16" width="3" height="2"/><rect x="14" y="16" width="3" height="2"/>
            </g>
          </svg>
          <span>842 61 937</span>
        </li>
      </ul>

      <div class="brand-block">
        <div class="brand-name"><span class="brand-dot"></span>Velora Hypnotherapy</div>
        <p class="brand-url">www.veloraclinicalhypnotherapy.com.au</p>
      </div>
    </section>

    <section class="card card-back" aria-label="Business card back with appointment space">
      <div class="back-header">
        <p class="back-title">Velora Clinical Hypnotherapy</p>
        <p>Appointment Phone: 0427 591 628</p>
        <p>12 Harlow Street, Kensington 3031</p>
        <p>www.veloraclinicalhypnotherapy.com.au</p>
      </div>
      <h2 class="appointments-title">Appointments</h2>
      <div class="appointment-grid">
        <div class="appointment-row"><span class="blank blank-date"></span>/<span class="blank blank-date"></span>/<span class="blank blank-date"></span><span class="blank blank-time"></span></div>
        <div class="appointment-row"><span class="blank blank-date"></span>/<span class="blank blank-date"></span>/<span class="blank blank-date"></span><span class="blank blank-time"></span></div>
        <div class="appointment-row"><span class="blank blank-date"></span>/<span class="blank blank-date"></span>/<span class="blank blank-date"></span><span class="blank blank-time"></span></div>
        <div class="appointment-row"><span class="blank blank-date"></span>/<span class="blank blank-date"></span>/<span class="blank blank-date"></span><span class="blank blank-time"></span></div>
        <div class="appointment-row"><span class="blank blank-date"></span>/<span class="blank blank-date"></span>/<span class="blank blank-date"></span><span class="blank blank-time"></span></div>
        <div class="appointment-row"><span class="blank blank-date"></span>/<span class="blank blank-date"></span>/<span class="blank blank-date"></span><span class="blank blank-time"></span></div>
      </div>
    </section>
  </main>
</body>
</html>
```